Tallowmere Riding School Flyer Design

We need a flyer for our Horse riding school, called Tallowmere Riding School.

At Tallowmere Riding School, Horses and ponies are carefully matched to suit each rider's experience, ability and confidence. I am a Qualified instructor, equipped to train all levels from nervous beginners to the more advanced.

Horse riding is fun! Riders, particularly children, are taught not only skills on the horse, but skills that are integral to good horsemanship and ownership of horses.

We regularly host Ladies Days, Guest Instructors, 1 hour Trail Rides and Pony Ride Days!

We teach people how to interact safely with, and care for horses so they develop a genuine love and respect for the animals and the sport.

In addition to fundamental riding techniques including walk, trot, and canter, we teach our students:
Grooming and Care of horses, Safety around horses, Balance and Co-Ordination, How to saddle up and care for Tack, Responsibility for equipment and horse, Confidence and Confidence Building for all Ages.

Private and group lessons start at 5 years of age upwards.

We recommend children 4 years and under partake in 15 minute pony rides, mainly due to their attention span!

Industry/Entity Type

School

```html
<!DOCTYPE html>
<html lang="en">
<head>
<meta charset="utf-8">
<title>Tallowmere Riding School Flyer</title>
<link rel="stylesheet" href="https://fonts.googleapis.com/css2?family=Quicksand:wght@500;600&display=swap">
<style>
  :root {
    --night: #1d2725;
    --night-soft: #2a3431;
    --fog: #7b8178;
    --field: #8a8a72;
    --field-dark: #5f6350;
    --chestnut: #a5552a;
    --chestnut-light: #c7773f;
    --teal: #4aa3b1;
    --teal-badge: #3c9dab;
    --panel: rgba(92, 160, 170, 0.55);
    --ink: #ffffff;
  }
  * { box-sizing: border-box; margin: 0; padding: 0; }
  html, body { width: 850px; height: 1200px; overflow: hidden; }
  body { font-family: "Quicksand", sans-serif; color: var(--ink); background: var(--night); }

  .flyer {
    position: relative;
    width: 850px;
    height: 1200px;
    overflow: hidden;
    background: linear-gradient(180deg, var(--night) 0%, var(--night-soft) 30%, #3b4540 40%, var(--fog) 50%, var(--field) 62%, var(--field-dark) 100%);
  }

  .field-photo {
    position: absolute;
    left: 0; top: 430px;
    width: 850px; height: 770px;
    background:
      radial-gradient(ellipse 300px 360px at 640px 440px, var(--chestnut-light) 0%, var(--chestnut) 45%, rgba(165, 85, 42, 0) 100%),
      radial-gradient(ellipse 420px 260px at 300px 620px, rgba(165, 85, 42, 0.85) 0%, rgba(165, 85, 42, 0) 100%),
      linear-gradient(180deg, rgba(110, 118, 108, 0) 0%, var(--fog) 20%, var(--field) 45%, var(--field-dark) 100%);
  }

  .frame {
    position: absolute;
    left: 48px; top: 43px;
    width: 760px; height: 1117px;
    pointer-events: none;
  }

  .brand {
    position: absolute;
    top: 30px; left: 0;
    width: 850px;
    text-align: center;
    font-weight: 500;
    color: var(--ink);
  }
  .brand-mark {
    display: block;
    width: 110px; height: 110px;
    margin: 0 auto 40px;
    border: 2px solid var(--ink);
    border-radius: 50%;
  }
  .brand-name {
    display: block;
    font-size: 36px;
    letter-spacing: 7px;
    line-height: 1;
  }
  .brand-sub {
    display: block;
    margin-top: 18px;
    font-size: 16px;
    letter-spacing: 4px;
  }

  .intro {
    position: absolute;
    left: 205px; top: 293px;
    width: 440px; height: 365px;
    padding: 18px 16px 0 16px;
    background: var(--panel);
    box-shadow: 0 0 24px 14px var(--panel);
    font-size: 17.5px;
    font-weight: 500;
    line-height: 24px;
    text-align: justify;
  }
  .intro p + p { margin-top: 24px; }

  .offers-badge {
    position: absolute;
    left: 156px; top: 898px;
    width: 162px; height: 162px;
    border-radius: 50%;
    background: var(--teal-badge);
    border: 3px solid var(--ink);
    display: flex;
    align-items: center;
    justify-content: center;
    text-align: center;
    font-size: 17px;
    font-weight: 500;
    line-height: 21px;
  }

  .contact {
    position: absolute;
    left: 75px; top: 1078px;
    font-weight: 600;
    text-shadow: 0 2px 4px rgba(0, 0, 0, 0.6);
  }
  .contact-address { font-size: 19px; }
  .contact-phone {
    margin: 16px 0 0 25px;
    font-size: 31px;
    letter-spacing: 1px;
  }
</style>
</head>
<body>
  <main class="flyer">
    <div class="field-photo" role="img" aria-label="Photograph of a chestnut pony with a white blaze and halter standing in a misty grassy field"></div>

    <svg class="frame" width="760" height="1117" viewBox="0 0 760 1117" aria-hidden="true">
      <path d="M300 1 H1 V1116 H759 V1 H460" fill="none" stroke="var(--teal)" stroke-width="2"/>
    </svg>

    <header class="brand">
      <span class="brand-mark" aria-hidden="true"></span>
      <span class="brand-name">TALLOWMERE</span>
      <span class="brand-sub">RIDING SCHOOL</span>
    </header>

    <section class="intro">
      <p>At Tallowmere Riding School, horses and ponies are carefully matched to suit each rider's experience, ability and confidence. I am a qualified instructor, tutoring from nervous beginners to the more advanced.</p>
      <p>I teach people how to interact safely with, and care for horses as so to develop a genuine love and respect for the animals and the sport.</p>
      <p>Private, group lessons and trail rides available, All ages catered for!</p>
    </section>

    <div class="offers-badge">
      <p>Ask about<br>Ladies Days,<br>Guest Instructors,<br>Trail Rides and<br>Pony Rides.</p>
    </div>

    <footer class="contact">
      <p class="contact-address">Find us on Brindle Rd, Larkhaven</p>
      <p class="contact-phone">Call&nbsp; 0400 555 018</p>
    </footer>
  </main>
</body>
</html>
```